Young Architect Bussiness Card

English is not my first language (spanish is).
Need a bussiness card design for my best friend who is about to graduate from college, Licentiate degree in architecture, so she needs business cards to start networking, currently she has no porfolio, web page or plazared. so she is relying on her cel phone and correovela, but should leave space for one of them (plazared)

Design for business card should be modern, maybe something with construction blue prints patern or 3D modelling.

Name: Mariela Otárola Bonilla
Licentiate in Arquitecture
Cel: (506) XXX-4827
email: marielaXXX@correovela.com

Services, although im not sure if it has to be there or not:
Anteproyectos / Proposal design
Inspecciones / Site Inspections
Modelado 3D / 3D modelling
Planos Constructivos / Construction Blue Prints
Presupuestos / Budgets

Design should be in spanish

Industry/Entity Type

Architect

Contact Information for Business Card

Name: Mariela Otárola, Arquitecto
Associtation code : XXXX
Phone: (506) XXXX-XXXX
Email: xxx@correovela.com
Plazared: xxxx

Requirements
Must have
• Design for business card should be modern, maybe something with construction blue prints patern or 3D modelling.
Nice to have
• Something like a transition from 2D to 3D.

```html
<!DOCTYPE html>
<html lang="es">
<head>
<meta charset="utf-8">
<title>Tarjeta de presentación — Mariela Otárola Bonilla</title>
<link href="https://fonts.googleapis.com/css2?family=Cinzel:wght@400;600&family=Cormorant+SC:wght@500;600&family=Cormorant+Garamond:wght@600&display=swap" rel="stylesheet">
<style>
  :root{
    --page:#2b2b2d;
    --card-sky:#bfe0e6;
    --card-render:#dde3ee;
    --card-paper:#e9e9e9;
    --ink:#141414;
    --brand-blue:#2a3fb4;
    --name-blue:#27337f;
    --rule:#c9c9c9;
    --roof:#d9953f;
    --plan:#f3f3f3;
    --on-blue:#ffffff;
  }
  *{margin:0;padding:0;box-sizing:border-box}
  html,body{width:1200px;height:903px;overflow:hidden;background:var(--page)}
  .sheet{position:relative;width:1200px;height:903px}
  .card{position:absolute;top:300px;width:530px;height:303px;border-radius:3px;overflow:hidden;box-shadow:0 10px 24px rgba(0,0,0,.45)}
  .card--services{left:50px}
  .card--identity{left:620px;background:var(--card-paper)}

  .render{position:absolute;inset:0;background:linear-gradient(160deg,var(--card-sky) 0%,var(--card-render) 45%,#c6cfe2 100%)}
  .services__title{position:absolute;left:0;right:0;top:34px;text-align:center;font-family:"Cinzel",serif;font-size:40px;font-weight:600;color:var(--ink);letter-spacing:1px}
  .services__list{position:absolute;left:28px;top:112px;list-style:none;font-family:"Cormorant SC",serif;font-weight:600;font-size:16px;color:var(--ink);line-height:24px}
  .services__list li{display:flex;align-items:center;gap:8px}
  .services__list svg{width:14px;height:14px;flex:none}
  .band{position:absolute;left:0;top:0;width:530px;height:303px}
  .services__email{position:absolute;right:24px;top:222px;font-family:"Cormorant Garamond",serif;font-size:19px;font-weight:600;color:var(--on-blue);white-space:nowrap}

  .identity__name{position:absolute;left:16px;top:122px;font-family:"Cinzel",serif;font-size:21px;font-weight:400;color:var(--name-blue);white-space:nowrap}
  .identity__bar{position:absolute;left:0;top:156px;width:318px;height:5px;background:var(--ink)}
  .identity__title{position:absolute;left:0;width:318px;top:166px;text-align:right;padding-right:12px;font-family:"Cormorant SC",serif;font-weight:600;font-size:16px;color:var(--ink)}
  .divider{position:absolute;left:318px;top:0;width:1px;height:303px;background:var(--rule)}
  .contact{position:absolute;right:226px;top:212px;text-align:right;font-family:"Cormorant SC",serif;font-weight:600;color:var(--ink);line-height:19px}
  .contact__row{display:flex;justify-content:flex-end;align-items:center;gap:8px;font-size:16px;white-space:nowrap}
  .contact__row svg{width:13px;height:13px;flex:none}
  .contact__row--small{font-size:14px;padding-right:21px}
  .plan{position:absolute;left:319px;top:0;width:211px;height:303px;background:linear-gradient(200deg,#e2e2e2 0%,var(--plan) 35%,#e8d2b4 62%,var(--roof) 78%,#e6e6e6 100%)}
</style>
</head>
<body>
<main class="sheet">

  <section class="card card--services" aria-label="Reverso: servicios">
    <div class="render" role="img" aria-label="Render arquitectónico en tonos celestes de un edificio moderno con árboles"></div>
    <svg class="band" viewBox="0 0 530 303" aria-hidden="true">
      <polygon points="0,268 220,268 262,212 530,212 530,303 0,303" fill="var(--brand-blue)"/>
    </svg>
    <h2 class="services__title">Services</h2>
    <ul class="services__list">
      <li><svg viewBox="0 0 14 14"><path d="M1 7 7 2l6 5M3 6v6h8V6" fill="none" stroke="#222" stroke-width="1.4"/></svg>Anteproyectos / Proposal design</li>
      <li><svg viewBox="0 0 14 14"><path d="M1 7 7 2l6 5M3 6v6h8V6" fill="none" stroke="#222" stroke-width="1.4"/></svg>Inspecciones / Site Inspections</li>
      <li><svg viewBox="0 0 14 14"><path d="M1 7 7 2l6 5M3 6v6h8V6" fill="none" stroke="#222" stroke-width="1.4"/></svg>Modelado 3D / 3D modelling</li>
      <li><svg viewBox="0 0 14 14"><path d="M1 7 7 2l6 5M3 6v6h8V6" fill="none" stroke="#222" stroke-width="1.4"/></svg>Planos Constructivos / Construction Blue Prints</li>
      <li><svg viewBox="0 0 14 14"><path d="M1 7 7 2l6 5M3 6v6h8V6" fill="none" stroke="#222" stroke-width="1.4"/></svg>Presupuestos / Budgets</li>
    </ul>
    <p class="services__email">marielaXXX@correovela.com</p>
  </section>

  <section class="card card--identity" aria-label="Frente: datos de contacto">
    <div class="plan" role="img" aria-label="Ilustración de planos arquitectónicos que pasan a un modelo 3D con techo naranja"></div>
    <div class="divider"></div>
    <h1 class="identity__name">Mariela Otárola Bonilla</h1>
    <div class="identity__bar"></div>
    <p class="identity__title">Licentiate in Arquitecture</p>
    <div class="contact">
      <p class="contact__row">(506) XXX-4827
        <svg viewBox="0 0 13 13"><rect x="0.5" y="0.5" width="12" height="12" fill="#222"/><path d="M3 4c0 3 3 6 6 6l1-2-2-1-1 1c-1-.5-2-1.5-2.5-2.5l1-1-1-2z" fill="#fff"/></svg></p>
      <p class="contact__row">marielaXXX@correovela.com
        <svg viewBox="0 0 13 13"><rect x="0.5" y="0.5" width="12" height="12" fill="#222"/><path d="M2.5 4h8v5h-8zM2.5 4l4 3 4-3" fill="none" stroke="#fff"/></svg></p>
      <p class="contact__row contact__row--small">Associtation code : XXXX</p>
      <p class="contact__row contact__row--small">Plazared: xxxx</p>
    </div>
  </section>

</main>
</body>
</html>
```